Flaschenetiketten-Design in rechteckiger Grundform für Biermanufaktur
Zielgruppe
Wir repräsentieren eine Bier-Manufaktur in der Gründungsphase und sind auf der Suche nach einem Designvorschlag für die Flaschenetiketten.
Unsere Zielgruppe sind Liebhaber, die auf der Suche nach dem Speziellen und Lokalen sind. Der Biergenuss abseits des Massenmarktes soll im Entwurf sichtbar/transportiert werden. Die Bier-Manufaktur steht zeitgleich für Trend-Kreationen mit bodenständigem Ursprung.
Aufgabenstellung
Die Herkunft der Gründer Familie aus dem Schweizer Kanton Simplon soll im Vordergrund stehen, hierzu bitte das Familienwappen / einzelne Elemente siehe Dateiupload berücksichtigen.
Das Etikett soll eine rechteckige Grundform haben.
Folgende Angaben sollen sich im Etikett wiederfinden:
- Biersorte: 'Lager' (zukünftig soll es möglich sein, Biersorte auf dem Etikett zu wechseln)
Brand: 'Hearty Kandrom'
'Biermanufaktur Walliser Ursprungs'
Die Schrift soll klar und nicht zu verspielt sein.

```html
<!DOCTYPE html>
<html lang="de">
<head>
<meta charset="utf-8">
<title>Hearty Kandrom – Lagerbier Etikett</title>
<link rel="stylesheet" href="https://fonts.googleapis.com/css2?family=Josefin+Sans:wght@600;700&display=swap">
<style>
  :root {
    --page: #ffffff;
    --slate: #6f7b93;
    --label-dark: #1d2529;
    --label-mid: #2c363b;
    --photo-warm: #4a4436;
    --photo-cool: #34424d;
    --ink-light: #ffffff;
  }
  html, body {
    margin: 0;
    padding: 0;
    width: 844px;
    height: 1200px;
    overflow: hidden;
    background: var(--page);
  }
  .canvas {
    position: relative;
    width: 844px;
    height: 1200px;
    background: var(--page);
  }
  .label {
    position: absolute;
    left: 213px;
    top: 64px;
    width: 401px;
    height: 445px;
    box-sizing: border-box;
    border: 7px solid var(--slate);
    background: var(--label-dark);
    box-shadow: 4px 8px 16px rgba(0,0,0,0.35);
    overflow: hidden;
    font-family: "Josefin Sans", sans-serif;
    color: var(--ink-light);
  }
  .label__photo {
    position: absolute;
    inset: 0;
    background:
      radial-gradient(ellipse 45% 55% at 38% 62%, var(--photo-warm) 0%, rgba(74,68,54,0) 100%),
      radial-gradient(ellipse 60% 40% at 80% 40%, var(--photo-cool) 0%, rgba(52,66,77,0) 100%),
      linear-gradient(180deg, var(--label-dark) 0%, var(--label-mid) 45%, var(--label-dark) 100%);
  }
  .label__brandmark {
    position: absolute;
    left: 0;
    right: 0;
    top: 95px;
    display: flex;
    justify-content: center;
    align-items: center;
    gap: 8px;
    font-weight: 600;
    font-size: 15px;
    line-height: 15px;
    letter-spacing: 2px;
    color: var(--slate);
  }
  .label__brandmark-square {
    width: 12px;
    height: 12px;
    background: var(--slate);
  }
  .label__variety {
    position: absolute;
    left: 0;
    right: 0;
    top: 183px;
    text-align: center;
    font-weight: 600;
    font-size: 14px;
    line-height: 14px;
    letter-spacing: 1.6px;
  }
  .label__name {
    position: absolute;
    left: 0;
    right: 0;
    top: 270px;
    margin: 0;
    text-align: center;
    font-weight: 600;
    font-size: 56px;
    line-height: 54px;
    letter-spacing: 3px;
  }
  .label__tagline {
    position: absolute;
    left: 0;
    right: 0;
    top: 389px;
    text-align: center;
    font-weight: 600;
    font-size: 12px;
    line-height: 12px;
    letter-spacing: 1.5px;
  }
</style>
</head>
<body>
<main class="canvas">
  <section class="label">
    <div class="label__photo" role="img" aria-label="Abgedunkeltes Foto eines steinernen Denkmals in verschneiter Berglandschaft"></div>
    <div class="label__brandmark"><span class="label__brandmark-square"></span>HEARTY KANDROM</div>
    <div class="label__variety">- LAGERBIER -</div>
    <h1 class="label__name">HEARTY<br>KANDROM</h1>
    <div class="label__tagline">BIERMANUFAKTUR WALLISER URSPRUNGS</div>
  </section>
</main>
</body>
</html>
```